Children’s entertainer/balloon artist Website Home Page and custom landing page

I need a home page design for the home page of a children and family entertainer/balloon twister’s website. I also need a custom landing page for family theatre shows performed by the same entertainer.
It will be a Wordpress website and I need the final artwork in a layer Photoshop file with all the layers clearly named and labeled.

Target Market(s)

The site visitors are mainly mums, aged between early 20’s and late 30’s. Other visitors will included companies for Christmas functions, and event organisers for corporate functions.

Industry/Entity Type

Entertainment

Number of Pages Required

2 page

Font styles to use
Sans Serif

Colors
34a6d7
f37122

Requirements
Must have
• Layout
• I have included a wireframe for the home page layout and the custom landing page for your reference. This is a guide only and I welcome your interpretation with the rough layout provided.
• This website needs to look good on all devices as it will be fully responsive.
• It needs to include a footer area on the page, that has social media and a call to action area included.
• Colours
• The main colours for the site is:
• orange (call to action colour)
• ff6800
• blue/turquoise
• 42abc3
• Pictures
• I have included images of the entertainer/balloon artist for you to use/take inspiration from.
• These images will be included on the website. I want to show lots of people having fun.
• I would like to have elements of the logo used in isolation across the website
• i.e. the octopus figure to be included in the footer or the bird element to be included in the testimonial slider etc.
• Elements to include
• Note: use the images of the entertainer in the boxes on the home page (balloon shows, balloon twisting, balloon workshops, theatre shows (the three little balloon pigs on his head)
Nice to have
Should not have
• Element to avoid
• Stock imagery of balloon sculptures - use images provided.

```html
<!DOCTYPE html>
<html lang="en">
<head>
<meta charset="utf-8">
<title>Benny Balloons – Children's Entertainer</title>
<link href="https://fonts.googleapis.com/css2?family=Open+Sans:wght@300;400;600;700&family=Raleway:wght@300;400;600;700&display=swap" rel="stylesheet">
<style>
:root{
  --blue:#1f74c4;
  --blue-deep:#0f4f98;
  --blue-light:#3a9ee6;
  --orange:#f37122;
  --orange-dark:#d95a10;
  --green:#5cbf2a;
  --card-blue:#2f8fd6;
  --purple:#8a2ec4;
  --navy:#1c2f55;
  --ink:#3b3b3b;
  --muted:#7a7a7a;
  --white:#ffffff;
}
*{box-sizing:border-box;margin:0;padding:0}
html,body{width:717px;height:1200px;overflow:hidden}
body{
  font-family:"Open Sans",Arial,sans-serif;
  color:var(--ink);
  background:radial-gradient(ellipse at 50% 10%, var(--blue-light) 0%, var(--blue) 45%, var(--blue-deep) 100%);
  position:relative;
}
.site-header{height:140px;display:flex;align-items:center;justify-content:center}
.brand{display:flex;align-items:center;gap:10px;color:var(--white);font-family:"Raleway",sans-serif;font-weight:700;font-size:26px}
.brand-dot{width:26px;height:26px;border-radius:50%;background:var(--orange)}
.main-nav{position:absolute;top:142px;left:0;width:717px;height:28px;background:var(--orange)}
.main-nav ul{list-style:none;display:flex;margin-left:60px;height:100%}
.main-nav li{font-size:8.5px;font-weight:600;color:var(--white);letter-spacing:.4px;padding:0 15px;line-height:28px;text-transform:uppercase}
.main-nav li.active{background:var(--orange-dark);border-left:1px solid rgba(255,255,255,.4);border-right:1px solid rgba(255,255,255,.4)}
.container{position:absolute;left:60px;width:597px}
.hero{top:190px;height:370px;background:var(--white);box-shadow:0 4px 14px rgba(0,0,0,.25)}
.hero-photo{position:relative;height:270px;background:linear-gradient(110deg,#e8edf3 0%,#9fb3cf 35%,#34507f 60%,var(--navy) 100%)}
.hero-caption{position:absolute;right:30px;top:45px;width:210px;color:var(--white)}
.hero-caption .first{font-family:"Raleway",sans-serif;font-size:34px;font-weight:400;letter-spacing:1px;line-height:1}
.hero-caption .last{font-family:"Raleway",sans-serif;font-size:20px;font-weight:300;margin-top:4px}
.hero-caption p{font-size:7.5px;line-height:1.5;margin-top:10px;opacity:.9}
.slider-arrows{position:absolute;right:16px;bottom:14px;display:flex;gap:8px}
.slider-arrows svg{width:14px;height:14px}
.testimonial{display:flex;align-items:center;gap:16px;padding:14px 18px;height:100px}
.quote{flex:1;font-size:7.5px;line-height:1.6;color:var(--muted)}
.quote .mark{color:var(--orange);font-size:14px;font-weight:700;line-height:0;vertical-align:-3px;margin-right:3px}
.quote cite{display:block;margin-top:6px;font-style:italic;color:var(--ink)}
.btn{display:inline-block;font-size:8px;font-weight:600;text-transform:uppercase;color:var(--white);padding:8px 14px;letter-spacing:.5px}
.btn-orange{background:var(--orange)}
.btn-blue{background:var(--blue)}
.about{top:580px;height:195px;background:var(--white);padding:16px;display:flex;gap:16px}
.about-photo{width:150px;height:163px;background:linear-gradient(160deg,#b9cde0,#4a6f9a 70%,#2a3e5c)}
.about-text{flex:1}
.about-text h2{font-family:"Raleway",sans-serif;font-weight:300;font-size:24px;color:var(--ink);margin:2px 0 8px}
.about-text p{font-size:7.5px;line-height:1.55;color:var(--muted);margin-bottom:8px}
.insta{width:140px;border:1px solid #e2e2e2;padding:6px}
.insta h3{font-size:8px;font-weight:600;text-align:center;padding:4px 0 8px;border-bottom:1px solid #e2e2e2;margin-bottom:6px;display:flex;align-items:center;justify-content:center;gap:5px}
.insta h3 span{width:8px;height:8px;border-radius:2px;background:var(--blue)}
.insta-grid{display:grid;grid-template-columns:repeat(4,1fr);gap:3px}
.insta-grid div{aspect-ratio:1;background:linear-gradient(135deg,#f4b27a,#c55a8c)}
.insta-grid div:nth-child(3n){background:linear-gradient(135deg,#7fc4ef,#3a63a8)}
.insta-grid div:nth-child(4n+2){background:linear-gradient(135deg,#f7e07a,#e57b34)}
.services{top:795px;height:230px;display:grid;grid-template-columns:repeat(4,1fr);gap:12px}
.service{display:flex;flex-direction:column}
.service-photo{height:110px}
.service-body{flex:1;color:var(--white);text-align:center;padding:10px 10px 0;clip-path:polygon(0 0,100% 0,100% 88%,50% 100%,0 88%)}
.service-body h4{font-size:9px;font-weight:700;text-transform:uppercase;margin-bottom:6px}
.service-body p{font-size:7px;line-height:1.5;opacity:.95}
.service-body .more{display:block;font-size:6.5px;font-weight:700;margin-top:10px;text-transform:uppercase;letter-spacing:.5px}
.s-shows .service-photo{background:linear-gradient(135deg,#f6c75a,#e8508f)}
.s-shows .service-body{background:var(--orange)}
.s-twisting .service-photo{background:linear-gradient(135deg,#9ad86a,#e7476a)}
.s-twisting .service-body{background:var(--green)}
.s-workshops .service-photo{background:linear-gradient(135deg,#f0c23d,#3c78c4)}
.s-workshops .service-body{background:var(--card-blue)}
.s-theatre .service-photo{background:linear-gradient(135deg,#d43b6e,#3a2f8a)}
.s-theatre .service-body{background:var(--purple)}
.newsletter{position:absolute;top:1040px;left:0;width:717px;height:60px;background:var(--orange);display:flex;align-items:center;padding:0 60px;gap:16px}
.newsletter-icon{width:26px;height:26px;border-radius:50%;background:rgba(255,255,255,.25)}
.newsletter-text{flex:1;color:var(--white)}
.newsletter-text h5{font-size:11px;font-weight:700;text-transform:uppercase;letter-spacing:.5px}
.newsletter-text p{font-size:7px;opacity:.9;margin-top:2px}
.newsletter-form{display:flex}
.newsletter-form .field{width:110px;height:22px;background:var(--white);font-size:7px;color:#999;padding:0 8px;line-height:22px}
.newsletter-form .btn{padding:0 12px;line-height:22px}
.site-footer{position:absolute;top:1100px;left:0;width:717px;height:100px;background:var(--blue-deep);text-align:center;color:var(--white);padding-top:12px}
.social{display:flex;justify-content:center;gap:6px;margin-bottom:9px}
.social span{width:16px;height:16px;border-radius:50%;background:var(--white)}
.footer-links{font-size:7.5px;margin-bottom:5px}
.footer-contact,.copyright{font-size:7px;opacity:.85;margin-bottom:4px}
</style>
</head>
<body>
<header class="site-header">
  <div class="brand"><span class="brand-dot"></span>Benny Balloons</div>
</header>

<nav class="main-nav">
  <ul>
    <li class="active">Home</li>
    <li>Balloon Shows</li>
    <li>Balloon Twisting</li>
    <li>Theatre</li>
    <li>Reviews</li>
    <li>Contact Us</li>
  </ul>
</nav>

<section class="container hero">
  <div class="hero-photo" role="img" aria-label="Entertainer wearing a tall colourful balloon hat and holding balloon sculptures">
    <div class="hero-caption">
      <div class="first">BENNY</div>
      <div class="last">Hartwell</div>
      <p>Fun balloon shows, twisting and theatre for parties, schools and family events. Laughter and bright colours guaranteed every time.</p>
    </div>
    <div class="slider-arrows">
      <svg viewBox="0 0 14 14"><path d="M9 2 4 7l5 5" fill="none" stroke="#fff" stroke-width="2"/></svg>
      <svg viewBox="0 0 14 14"><path d="M5 2l5 5-5 5" fill="none" stroke="#fff" stroke-width="2"/></svg>
    </div>
  </div>
  <div class="testimonial">
    <div class="quote">
      <span class="mark">“</span>Benny made our daughter's birthday party truly unforgettable. The children laughed from start to finish, every guest went home with a balloon animal, and the parents enjoyed the show just as much as the kids. We have already booked him again for next year and will happily recommend him to friends.
      <cite>Jane Parker – Benny Hartwell</cite>
    </div>
    <span class="btn btn-orange">Book My Show</span>
  </div>
</section>

<section class="container about">
  <div class="about-photo" role="img" aria-label="Entertainer performing on stage beside a screen"></div>
  <div class="about-text">
    <h2>About Our Company</h2>
    <p>We bring colour, laughter and balloon magic to birthday parties, schools, festivals and corporate events. Every show is packed with interaction, giant balloon creations and plenty of silly surprises for all ages.</p>
    <p>From small family gatherings to big Christmas functions, each performance is tailored to your guests so that everyone, young and old, leaves with a smile and a memory.</p>
    <span class="btn btn-blue">Read More</span>
  </div>
  <aside class="insta">
    <h3><span></span>INSTAGRAM</h3>
    <div class="insta-grid" role="img" aria-label="Grid of party and balloon photos">
      <div></div><div></div><div></div><div></div>
      <div></div><div></div><div></div><div></div>
      <div></div><div></div><div></div><div></div>
    </div>
  </aside>
</section>

<section class="container services">
  <article class="service s-shows">
    <div class="service-photo" role="img" aria-label="Children enjoying a balloon show"></div>
    <div class="service-body"><h4>Balloon Shows</h4><p>Big, bright and funny shows packed with giant balloons and laughs.</p><span class="more">Learn More</span></div>
  </article>
  <article class="service s-twisting">
    <div class="service-photo" role="img" aria-label="Entertainer twisting balloon sculptures for guests"></div>
    <div class="service-body"><h4>Balloon Twisting</h4><p>Custom balloon animals and hats made fresh for every guest.</p><span class="more">Learn More</span></div>
  </article>
  <article class="service s-workshops">
    <div class="service-photo" role="img" aria-label="Group balloon workshop"></div>
    <div class="service-body"><h4>Balloon Workshops</h4><p>Hands-on sessions where kids learn to twist their own creations.</p><span class="more">Learn More</span></div>
  </article>
  <article class="service s-theatre">
    <div class="service-photo" role="img" aria-label="Family theatre show on a lit stage"></div>
    <div class="service-body"><h4>Theatre Shows</h4><p>Family theatre stories told with balloons, music and fun.</p><span class="more">Learn More</span></div>
  </article>
</section>

<section class="newsletter">
  <span class="newsletter-icon"></span>
  <div class="newsletter-text">
    <h5>Join Our Newsletter</h5>
    <p>Sign up for news, show dates and special party offers sent straight to your inbox.</p>
  </div>
  <div class="newsletter-form">
    <span class="field">Enter your E-Mail</span>
    <span class="btn btn-blue">Subscribe</span>
  </div>
</section>

<footer class="site-footer">
  <div class="social"><span></span><span></span><span></span><span></span><span></span></div>
  <div class="footer-links">Home | Balloon Shows | Balloon Twisting | Theatre | Reviews | Contact Us</div>
  <div class="footer-contact">Phone: 0123 456 789 | Email: hello@bennyballoons.example</div>
  <div class="copyright">Copyright © Benny Hartwell 2024. All rights reserved.</div>
</footer>
</body>
</html>
```